Business Card Design Project for a Restaurant/Wine Bar

New, fresh business card design for Brevenna Wine Bar & Restaurant, Bandon, Oregon. We are an established restaurant on the Oregon coast featuring "Italian coastal cuisine."

"Brevenna" means bay leaf in Italian. We aren't sure if we would like our logo on the card or not, but if you have something interesting that uses it, then please do so. The basic information is essential - full restaurant name, address, phone and website (do not use www). The font on our menu and wine list may give you some sort of an idea of our style.

One-sided card needed as we often use the backside to write down various types of info for customers.
Updates

After seeing a few submissions, we would like to see what designers can come up with-using the logo, just the leaf, or none at all. Sky is the limit as long as our full restaurant name, address, phone and website (please leave out www) are there. Please contact us if questions!

I appreciate all of your designs! Our deadline is next week, but I will continue to give feedback on designs as I can. This is our busiest season, so my co-owner/chef/husband, won't have time to look at the designs for awhile. When he does, we can make our decision.

cheers,
Maren

Target Market(s)

Fine dining/wine crowd. Would like something simple and elegant, but not pretentious or stuffy. Brevenna means bay laurel (bay leaf) in Italian (please see our logo).

Industry/Entity Type

Restaurant

Requirements
Must have
• Full Name of Restaurant: Brevenna Wine Bar & Restaurant
Address: 812 4th Ave NW, Marlow Cove, OR 97000
Phone: 541.555.0172
website: brevennawinebar.example (do not use www)
Should not have
• Loud colors.

```html
<!DOCTYPE html>
<html lang="en">
<head>
<meta charset="utf-8">
<title>Brevenna Wine Bar &amp; Restaurant — Business Card</title>
<link rel="stylesheet" href="https://fonts.googleapis.com/css2?family=Cinzel:wght@500&family=Arimo:wght@400&display=swap">
<style>
  :root {
    --page: #ffffff;
    --card: #ffffff;
    --olive-deep: #566a40;
    --olive-light: #919d74;
    --name-green: #5b6e46;
    --ink: #333333;
    --on-dark: #ffffff;
  }
  html, body {
    margin: 0;
    width: 1200px;
    height: 901px;
    overflow: hidden;
    background: var(--page);
  }
  .card {
    position: absolute;
    left: 141px;
    top: 188px;
    width: 919px;
    height: 525px;
    background: var(--card);
    overflow: hidden;
  }
  .card__waves {
    position: absolute;
    inset: 0;
    width: 100%;
    height: 100%;
  }
  .brand__name {
    position: absolute;
    left: 83px;
    top: 134px;
    margin: 0;
    font-family: "Cinzel", "Times New Roman", serif;
    font-weight: 500;
    font-size: 72px;
    line-height: 1;
    color: var(--name-green);
  }
  .brand__rule {
    position: absolute;
    left: 36px;
    top: 228px;
    width: 476px;
    height: 2px;
    background: var(--name-green);
  }
  .brand__tagline {
    position: absolute;
    left: 86px;
    top: 246px;
    margin: 0;
    font-family: "Arimo", Arial, sans-serif;
    font-size: 37.5px;
    line-height: 1;
    color: var(--ink);
  }
  .contact {
    position: absolute;
    left: 589px;
    top: 355px;
    margin: 0;
    font-family: "Arimo", Arial, sans-serif;
    font-style: normal;
    font-size: 22px;
    line-height: 31px;
    color: var(--on-dark);
  }
  .contact__line { display: flex; align-items: center; gap: 6px; }
  .contact__line--gap { margin-top: 6px; }
  .contact__icon { width: 18px; height: 18px; flex: none; }
</style>
</head>
<body>
  <article class="card">
    <svg class="card__waves" viewBox="0 0 689 394" preserveAspectRatio="none" aria-hidden="true">
      <path fill="var(--olive-light)" d="M0 254 C120 276 260 322 410 262 S610 128 689 170 L689 394 L0 394 Z"/>
      <path fill="var(--olive-deep)" d="M0 270 C130 298 270 322 420 276 S625 156 689 186 L689 394 L0 394 Z"/>
    </svg>

    <h1 class="brand__name">Brevenna</h1>
    <div class="brand__rule"></div>
    <p class="brand__tagline">Wine Bar &amp; Restaurant</p>

    <address class="contact">
      <div class="contact__line">812 4th Ave NW</div>
      <div class="contact__line">Marlow Cove, OR 97000</div>
      <div class="contact__line contact__line--gap">
        <svg class="contact__icon" viewBox="0 0 24 24" aria-hidden="true"><path fill="currentColor" d="M6.6 10.8a15.1 15.1 0 0 0 6.6 6.6l2.2-2.2c.3-.3.7-.4 1-.2 1.1.4 2.3.6 3.6.6.6 0 1 .4 1 1V20c0 .6-.4 1-1 1A17 17 0 0 1 3 4c0-.6.4-1 1-1h3.5c.6 0 1 .4 1 1 0 1.3.2 2.5.6 3.6.1.3 0 .7-.2 1z"/></svg>
        <span>541.555.0172</span>
      </div>
      <div class="contact__line">
        <svg class="contact__icon" viewBox="0 0 24 24" aria-hidden="true"><g fill="none" stroke="currentColor" stroke-width="2"><circle cx="12" cy="12" r="9"/><ellipse cx="12" cy="12" rx="4" ry="9"/><path d="M3 12h18M5 7h14M5 17h14"/></g></svg>
        <span>brevennawinebar.example</span>
      </div>
    </address>
  </article>
</body>
</html>
```